New Bicycle shop business card

Hi!
I'm looking for a business card for my new proffesional bike mechanics shop. This shop is only for fixing broken bikes and not selling bikes.
Peferbly a modern and sleek and modern design.
Colors: black, grey, red, white
Information:
Name: Rijwielwerkplaats Vanhoutte
Shop owner: Bart Vanhoutte & Marieke Segers
Website: www.rijwielwerkplaats-vanhoutte.be
Email: info@rijwielwerkplaats-vanhoutte.be
Phone number: +32471902368
Street adres: Kerkweg 46
9940 Bellebeke
Slogan/shop information: Herstellingen van alle merken.
Logo: see files.
Target Market(s)
People who seek a mechanic to fix or upgrade their bikes.
Contact Information for Business Card
Information:
Website: info@rijwielwerkplaats-vanhoutte.be
9940 Bellebeke
Logo: see files.

```html
<!DOCTYPE html>
<html lang="nl">
<head>
<meta charset="utf-8">
<title>Rijwielwerkplaats Vanhoutte – visitekaartje</title>
<link rel="stylesheet" href="https://fonts.googleapis.com/css2?family=Montserrat:wght@400;500;700;800&display=swap">
<style>
  :root {
    --stage: #18181a;
    --card: #242528;
    --red: #e31d3f;
    --white: #ffffff;
    --grey: #d9d9dc;
  }
  * { margin: 0; padding: 0; box-sizing: border-box; }
  html, body {
    width: 1200px; height: 800px; overflow: hidden;
    background: var(--stage);
    font-family: "Montserrat", sans-serif;
  }
  .stage { position: relative; width: 1200px; height: 800px; }

  .card {
    position: absolute;
    width: 540px; height: 320px;
    background: var(--card);
    border-radius: 3px;
    box-shadow: 0 18px 40px rgba(0,0,0,.55);
    overflow: hidden;
  }
  .card--front { left: 50px; top: 80px; }
  .card--back  { left: 610px; top: 400px; }

  .brand {
    display: flex; align-items: center; gap: 12px;
  }
  .brand__dot {
    width: 34px; height: 34px; border-radius: 50%;
    background: var(--red); flex: none;
  }
  .brand__name {
    color: var(--white);
    font-weight: 800;
    font-size: 20px;
    line-height: 1.1;
    letter-spacing: .04em;
    text-transform: uppercase;
  }

  /* front */
  .front__content {
    position: absolute; left: 150px; top: 110px;
  }
  .front__slogan {
    margin-top: 14px;
    color: var(--white);
    font-size: 15px; font-weight: 500;
    letter-spacing: .02em;
  }

  /* back */
  .back__brand {
    position: absolute; left: 0; right: 0; top: 46px;
    justify-content: center;
  }
  .back__rule {
    position: absolute; top: 196px; height: 8px; background: var(--red);
  }
  .back__rule--left  { left: 0; width: 92px; }
  .back__rule--right { left: 448px; right: 0; }
  .contact {
    position: absolute; left: 0; right: 0; top: 134px;
    text-align: center;
    color: var(--grey);
    font-size: 11px; line-height: 1.75; font-weight: 500;
  }
  .contact__owners { color: var(--white); text-transform: uppercase; letter-spacing: .02em; }
  .contact__label { color: var(--red); }
  .contact__web { color: var(--red); }
  .back__band {
    position: absolute; left: 0; right: 0; bottom: 0; height: 48px;
    background: var(--red);
    display: flex; align-items: center; justify-content: center;
    color: var(--white); font-size: 15px; font-weight: 700; letter-spacing: .02em;
  }
</style>
</head>
<body>
<main class="stage">
  <section class="card card--front" aria-label="Voorzijde visitekaartje">
    <div class="front__content">
      <div class="brand">
        <span class="brand__dot"></span>
        <span class="brand__name">Rijwielwerkplaats<br>Vanhoutte</span>
      </div>
      <p class="front__slogan">Herstellingen van alle merken</p>
    </div>
  </section>

  <section class="card card--back" aria-label="Achterzijde visitekaartje">
    <div class="brand back__brand">
      <span class="brand__dot"></span>
      <span class="brand__name">Rijwielwerkplaats<br>Vanhoutte</span>
    </div>
    <div class="back__rule back__rule--left"></div>
    <div class="back__rule back__rule--right"></div>
    <address class="contact" style="font-style:normal">
      <div class="contact__owners">Bart Vanhoutte &amp; Marieke Segers</div>
      <div><span class="contact__label">P:</span> +32471902368 | <span class="contact__label">E:</span> info@rijwielwerkplaats-vanhoutte.be</div>
      <div class="contact__web">www.rijwielwerkplaats-vanhoutte.be</div>
      <div>Kerkweg 46, 9940 Bellebeke</div>
    </address>
    <div class="back__band">Herstellingen van alle merken</div>
  </section>
</main>
</body>
</html>
```